Trailhead Cove Website - Sell Outdoor product

We are a mom and pop company that just opened our website.

We need a fresh, professional, and nice looking website for our outdoor products. We sell hunting, camping, fishing, and hiking products/accessories to name a few. Some of these products are optics, gun safes, gun bi-pods and tripods, gun lights, hunting camera, tents, hearing protection, targets, fishing poles, and hiking backpacks to name a few.

Our current website is: http://www.trailheadcove-example.com . You'll see our logo on the website, and it is attached. We aren't married to this logo, so if the designer thinks they can modify it or even come up with a better design for the website, they are more than welcome to do so. We need someone with good images of their own (clip art and/or outdoor images) they can use if they need to for our website.

I also attached a idea I had in plandraw, but please don't think this is set in stone. It is just a very rough idea. You can also go to our bazarro site to see what we sell: www.bazarro-example.com/shops/k9qz311mrtxn4p . Right now we sell everything on Bazarro, but our website will just focus on outdoor product. So please make it an outdoor focused website. And you can be creative with some of the product category names. We also want to leave room for some parallel product in the future. Like garden tools, back yard furniture, and BBQs.

Our company also wants to include a deals section on the website. We will probably update it once a week or month. I have included what I did for a deal and accompanying images for it. Image is called Morvelid (And the main images are 01 and 02).

We also want to make sure the file is compatible with our current web-hosting company, https://www.hostlyne-example.com. So I included a webpage layout zip folder. If you have any questions, please contact me.

This is for a PSD and HTML/CSS webpage. If you have any artwork or images that you own and want to use them for the webpage, please do so.

Target Market(s)

The hunter, outdoors person, camper, hiker, and etc.

Industry/Entity Type

It Company

Coding

Coded - Design and coding required

Number of Pages Required

3 page

Requirements
Must have
• The main page. PSD and HTML/CSS file.
• The category page. PSD and HTML/CSS file
• The product display page. PSD and HTML/CSS file
• Please also use some images that you have or from the sites below:
• You can get free stock images for 7 days (20 per day) from this site:
• https://www.pixelvault-example.com/complimentary/PVXTRL/?utm_source=PVXTrialFT&utm_medium=cpc&utm_campaign=PVXTrialFT&gclid=QWRt5mnBkdTRZpLoWsePb7uVbQ
• Has 14 good sites:
• http://www.venturedesk-example.com/article/517293
• Here are the ones I like:
• https://clearshot-example.com/
• http://brightwide-example.com/
• http://www.sitebloom-example.com/free/nature
• http://www.pictorium-example.com/archive
• http://tinyframes-example.co/
• http://old.vintlens-example.co/search/hiking
• http://fetchpix.blogsite-example.com/
• http://rolvenpask-example.com/post/584920173645/download
• http://openimagevault-example.com/
• If there is a photographer listed on or next to the image, on the bottom lower corner of the image, please put the photographer's name.
Nice to have
• I would like to have an unsubscribe page. If the designer has any of their own images of the outdoor world, and they want to use them, please do. Just make the right graphic changes to make it look good.
Should not have
• Try and keep green color to a minimum.

```html
<!DOCTYPE html>
<html lang="en">
<head>
<meta charset="utf-8">
<title>Trailhead Cove – Outdoor Gear</title>
<link rel="stylesheet" href="https://fonts.googleapis.com/css2?family=Montserrat:wght@400;500;600;700;800&family=Open+Sans:wght@400;600;700&display=swap">
<style>
:root{
  --ink:#1d1d1d;
  --muted:#555;
  --topbar:#f1f1f1;
  --gold-1:#ffc20e;
  --gold-2:#fba51a;
  --orange:#f7941d;
  --divider:#c98a0a;
  --card-line:#d6d6d6;
  --card-foot:#f0f0f0;
  --buy:#3fbf1f;
  --footer:#0a0a0a;
  --footer-text:#bdbdbd;
  --white:#fff;
  --dot:#3ab7e8;
}
*{box-sizing:border-box;margin:0;padding:0}
html,body{width:810px;height:1200px;overflow:hidden;background:var(--white)}
body{position:relative;font-family:"Open Sans",Arial,sans-serif;color:var(--ink)}
a{color:inherit;text-decoration:none}

.topbar{position:absolute;left:0;top:0;width:810px;height:27px;background:var(--topbar);border-bottom:1px solid #dcdcdc;font-size:9px}
.topbar .newsletter{position:absolute;left:96px;top:8px}
.topbar .account{position:absolute;right:98px;top:8px;display:flex;gap:7px;align-items:center}
.topbar .account svg{margin-left:3px}

.brand{position:absolute;left:0;top:27px;width:810px;height:86px;display:flex;align-items:center;justify-content:center;gap:8px}
.brand .mark{width:16px;height:16px;background:var(--gold-1)}
.brand .name{font-family:"Montserrat",Arial,sans-serif;font-weight:800;font-size:24px;color:var(--ink);letter-spacing:1px;text-transform:uppercase}

.mainnav{position:absolute;left:0;top:113px;width:810px;height:36px;background:linear-gradient(#ffc716,var(--gold-2))}
.mainnav ul{list-style:none;position:absolute;left:104px;top:0;display:flex;height:36px}
.mainnav li{font-family:"Montserrat",Arial,sans-serif;font-weight:500;font-size:11.5px;line-height:36px;text-align:center;border-right:1px solid var(--divider)}
.mainnav li:last-child{border-right:none}

.hero{position:absolute;left:0;top:149px;width:810px;height:303px;background:linear-gradient(160deg,#d9cbb0 0%,#b48f62 35%,#7a5a3e 65%,#3d3127 100%);overflow:hidden}
.hero h1{position:absolute;left:0;width:810px;top:93px;text-align:center;font-weight:700;font-size:32px;color:var(--white);letter-spacing:-.5px;text-shadow:0 1px 3px rgba(0,0,0,.3)}
.hero h2{position:absolute;left:0;width:810px;top:138px;text-align:center;font-weight:600;font-size:22px;color:var(--white);text-shadow:0 1px 3px rgba(0,0,0,.3)}
.hero .dots{position:absolute;left:377px;top:279px;display:flex;gap:4px}
.hero .dots span{width:10px;height:10px;border-radius:50%;background:var(--white)}
.hero .dots span:first-child{background:var(--dot)}

.category-tile{position:absolute;top:474px;width:200px;height:116px;overflow:hidden}
.category-tile .label{position:absolute;left:0;bottom:0;width:100%;height:32px;background:rgba(30,30,30,.75);color:var(--white);font-size:13px;text-align:center;line-height:32px;text-transform:uppercase}
.tile-hunting{left:94px;background:linear-gradient(#e8e0cf,#b89a6a)}
.tile-hiking{left:305px;background:linear-gradient(#9fc0d8,#7d8a6c)}
.tile-fishing{left:516px;background:linear-gradient(#8fbf7a,#5f8a4a)}

.sidebar{position:absolute;left:94px;top:629px;width:148px;height:325px;background:linear-gradient(var(--gold-1),var(--orange));list-style:none}
.sidebar li{height:40.6px;border-bottom:1px solid rgba(180,110,0,.45);font-family:"Montserrat",Arial,sans-serif;font-weight:500;font-size:11.5px;padding-left:22px;line-height:40px;position:relative}
.sidebar li:last-child{border-bottom:none}
.sidebar li svg{position:absolute;right:12px;top:14px}

.product{position:absolute;width:147px;height:158px;border:1px solid var(--card-line);background:var(--white)}
.product .shot{position:absolute;left:0;top:0;width:100%;height:108px;display:flex;align-items:center;justify-content:center}
.product .shot span{display:block;width:60px;height:50px;border-radius:6px}
.product .info{position:absolute;left:0;top:108px;width:100%;height:49px;background:var(--card-foot);border-top:1px solid var(--card-line)}
.product .title{position:absolute;left:13px;top:6px;font-size:10.5px}
.product .price{position:absolute;left:13px;top:24px;font-size:13px}
.product .buy{position:absolute;right:6px;top:24px;width:59px;height:18px;background:var(--buy);color:var(--white);font-size:7.5px;text-align:center;line-height:18px}
.col1{left:252px}.col2{left:410px}.col3{left:569px}
.row1{top:629px}.row2{top:796px}

.footer{position:absolute;left:0;top:997px;width:810px;height:203px;background:var(--footer);color:var(--footer-text)}
.footer .col{position:absolute;top:30px}
.footer h3{font-weight:400;font-size:10.5px;color:var(--white);margin-bottom:6px}
.footer ul{list-style:none}
.footer li{font-size:7.2px;line-height:17px}
.footer .connect{font-size:7.5px;margin-bottom:7px}
.footer .social{display:flex;gap:4px;margin-bottom:10px}
.footer .social span{width:16px;height:16px;background:var(--white);border-radius:3px}
.footer .cards{display:flex;gap:3px}
.footer .cards span{width:21px;height:13px;background:#e8e8e8;border-radius:1px}
.footer .cards span.wide{width:36px}
.footer .rule{position:absolute;left:106px;top:160px;width:626px;height:1px;background:#2a2a2a}
.footer .copyright{position:absolute;left:106px;top:177px;font-size:7px;color:#7a7a7a}
</style>
</head>
<body>

<header class="topbar">
  <a class="newsletter" href="#">Join Our Newsletter</a>
  <nav class="account">
    <a href="#">My Account</a><span>|</span><a href="#">Login</a><span>|</span><a href="#">Shopping Cart</a>
    <svg width="14" height="12" viewBox="0 0 14 12"><path d="M0 1h2.5l2 7h7l2-5.5H4" fill="none" stroke="#222" stroke-width="1.6"/><circle cx="5.5" cy="10.5" r="1.2" fill="#222"/><circle cx="10.5" cy="10.5" r="1.2" fill="#222"/><path d="M4 2.5h9.5l-2 5.5h-6z" fill="#222"/></svg>
  </nav>
</header>

<div class="brand"><span class="mark"></span><span class="name">Trailhead Cove</span></div>

<nav class="mainnav">
  <ul>
    <li style="width:63px">Home</li>
    <li style="width:132px">Hunting Accessories</li>
    <li style="width:80px">Camping</li>
    <li style="width:64px">Fishing</li>
    <li style="width:64px">Hiking</li>
    <li style="width:120px">This Weeks Deals</li>
    <li style="width:70px">Brands</li>
  </ul>
</nav>

<section class="hero" role="img" aria-label="Photo of two hikers resting on a mountain ridge at sunset">
  <h1>MAURIS VEL LACUS VITAE</h1>
  <h2>CUM SOCIIS NATOQUE PENATI</h2>
  <div class="dots"><span></span><span></span><span></span><span></span></div>
</section>

<a class="category-tile tile-hunting" href="#" role="img" aria-label="Photo of a hunter in orange cap in tall grass"><span class="label">Hunting Products</span></a>
<a class="category-tile tile-hiking" href="#" role="img" aria-label="Photo of a couple sitting in a tent"><span class="label">Hiking Products</span></a>
<a class="category-tile tile-fishing" href="#" role="img" aria-label="Photo of a parent and child fishing by a lake"><span class="label">Fishing Products</span></a>

<ul class="sidebar">
  <li>Optics<svg width="7" height="13" viewBox="0 0 7 13"><path d="M1 1l5 5.5L1 12" fill="none" stroke="#8a5a00" stroke-width="1"/></svg></li>
  <li>Safes<svg width="7" height="13" viewBox="0 0 7 13"><path d="M1 1l5 5.5L1 12" fill="none" stroke="#8a5a00" stroke-width="1"/></svg></li>
  <li>Bipod and Tripods<svg width="7" height="13" viewBox="0 0 7 13"><path d="M1 1l5 5.5L1 12" fill="none" stroke="#8a5a00" stroke-width="1"/></svg></li>
  <li>Lights<svg width="7" height="13" viewBox="0 0 7 13"><path d="M1 1l5 5.5L1 12" fill="none" stroke="#8a5a00" stroke-width="1"/></svg></li>
  <li>Cameras<svg width="7" height="13" viewBox="0 0 7 13"><path d="M1 1l5 5.5L1 12" fill="none" stroke="#8a5a00" stroke-width="1"/></svg></li>
  <li>Tents<svg width="7" height="13" viewBox="0 0 7 13"><path d="M1 1l5 5.5L1 12" fill="none" stroke="#8a5a00" stroke-width="1"/></svg></li>
  <li>Ear Protection<svg width="7" height="13" viewBox="0 0 7 13"><path d="M1 1l5 5.5L1 12" fill="none" stroke="#8a5a00" stroke-width="1"/></svg></li>
  <li>Targets<svg width="7" height="13" viewBox="0 0 7 13"><path d="M1 1l5 5.5L1 12" fill="none" stroke="#8a5a00" stroke-width="1"/></svg></li>
</ul>

<article class="product col1 row1"><div class="shot" role="img" aria-label="Product photo of a battery pack"><span style="width:26px;height:70px;background:linear-gradient(#b8b8b8,#3a3a3a)"></span></div><div class="info"><span class="title">Product Name</span><span class="price">$25.55</span><a class="buy" href="#">Add To Cart</a></div></article>
<article class="product col2 row1"><div class="shot" role="img" aria-label="Product photo of a dome tent"><span style="width:80px;height:40px;background:linear-gradient(#8cc04a,#4a6e2a)"></span></div><div class="info"><span class="title">Product Name</span><span class="price">$25.55</span><a class="buy" href="#">Add To Cart</a></div></article>
<article class="product col3 row1"><div class="shot" role="img" aria-label="Product photo of a portable gun safe"><span style="width:82px;height:44px;background:linear-gradient(#555,#111)"></span></div><div class="info"><span class="title">Product Name</span><span class="price">$25.55</span><a class="buy" href="#">Add To Cart</a></div></article>
<article class="product col1 row2"><div class="shot" role="img" aria-label="Product photo of a rifle bipod"><span style="width:50px;height:76px;background:linear-gradient(#444,#111)"></span></div><div class="info"><span class="title">Product Name</span><span class="price">$25.55</span><a class="buy" href="#">Add To Cart</a></div></article>
<article class="product col2 row2"><div class="shot" role="img" aria-label="Product photo of blue ear muffs"><span style="width:56px;height:74px;border-radius:20px;background:linear-gradient(#2a2a2a,#2d5ea8)"></span></div><div class="info"><span class="title">Product Name</span><span class="price">$25.55</span><a class="buy" href="#">Add To Cart</a></div></article>
<article class="product col3 row2"><div class="shot" role="img" aria-label="Product photo of a small flashlight with clip"><span style="width:70px;height:24px;border-radius:10px;background:linear-gradient(#444,#0d0d0d)"></span></div><div class="info"><span class="title">Product Name</span><span class="price">$25.55</span><a class="buy" href="#">Add To Cart</a></div></article>

<footer class="footer">
  <div class="col" style="left:112px"><h3>COMPANY</h3><ul><li>Home</li><li>About US</li><li>FAQ</li><li>Blog</li><li>Shipping/Return</li></ul></div>
  <div class="col" style="left:234px"><h3>PRODUCTS</h3><ul><li>Morbi diam</li><li>Aauris viverra</li><li>Gravida mattis</li><li>Sonummy nibh ligula</li><li>pulvinar metus</li></ul></div>
  <div class="col" style="left:376px"><h3>RESOURCES</h3><ul><li>Privacy</li><li>Support</li><li>Terms &amp; Conditions</li><li>Contact Us</li></ul></div>
  <div class="col" style="left:509px"><h3>GET IN TOUCH</h3><p class="connect">Connect with us on social sites.</p>
    <div class="social"><span></span><span></span><span></span></div>
    <div class="cards"><span></span><span></span><span></span><span class="wide"></span></div>
  </div>
  <div class="rule"></div>
  <p class="copyright">© 2015 Company Name  All right reserved  Term of Use</p>
</footer>

</body>
</html>
```